Services Brochure

Hi Team
As mentioned, we have a requirement for some brochures for some of our services. Please see attachments for details.

File #1 - NOC Exec Summary.docx - Focused on the essential services (water and electricity) industry, Providing Operation Center services to client.
File #2 - Agnostic Support Brief.docx - Focused on providing Agnostic support of technology platforms for the aviation industry.
File #3 & #4 - Cyber 1.docx & Cyber 2.pdf - Focused on Cyber Security.

Please use design theme from our Company Profile project (TANSWELL-Technology-Services.pdf) for these brochures.
Can you please also leave text areas as text so it is easier for us to amend any mistakes on our end.

```html
<!DOCTYPE html>
<html lang="en">
<head>
<meta charset="utf-8">
<title>NOC Capabilities Framework – Tanswell Technology</title>
<link rel="stylesheet" href="https://fonts.googleapis.com/css2?family=Poppins:wght@500;700&family=Open+Sans:wght@400&display=swap">
<style>
  :root {
    --ink: #000000;
    --paper: #ffffff;
    --accent: #ec1c24;
    --glow: #7a0a0e;
    --sky: #6f9fd0;
    --haze: #d9d3c0;
    --sun: #f3c66a;
    --ember: #e08a1e;
  }
  * { margin: 0; padding: 0; box-sizing: border-box; }
  html, body { width: 1200px; height: 927px; overflow: hidden; background: var(--paper); }
  .brochure-cover {
    position: relative;
    width: 1200px;
    height: 927px;
    background: var(--paper);
    overflow: hidden;
  }
  .cover-panel {
    position: absolute;
    inset: 0 0 21px 0;
    background: var(--ink);
    overflow: hidden;
  }
  .brand {
    position: absolute;
    top: 76px;
    left: 0;
    width: 100%;
    display: flex;
    justify-content: center;
    align-items: center;
    gap: 16px;
  }
  .brand-square {
    width: 34px;
    height: 34px;
    background: var(--accent);
  }
  .brand-name {
    font-family: "Poppins", sans-serif;
    font-weight: 700;
    font-size: 46px;
    letter-spacing: 1px;
    color: var(--paper);
    line-height: 1;
  }
  .cover-title {
    position: absolute;
    top: 196px;
    left: 0;
    width: 100%;
    text-align: center;
    font-family: "Poppins", sans-serif;
    font-weight: 500;
    font-size: 47px;
    letter-spacing: 1px;
    color: var(--paper);
    line-height: 1.2;
  }
  .cover-title .title-accent { color: var(--accent); font-weight: 700; }
  .cover-intro {
    position: absolute;
    top: 262px;
    left: 150px;
    width: 900px;
    text-align: center;
    font-family: "Open Sans", sans-serif;
    font-size: 17.4px;
    line-height: 22px;
    color: var(--paper);
  }
  .cover-visual {
    position: absolute;
    left: 0;
    top: 430px;
    width: 1200px;
    height: 476px;
    display: block;
  }
</style>
</head>
<body>
  <main class="brochure-cover">
    <section class="cover-panel">
      <header class="brand">
        <span class="brand-square"></span>
        <span class="brand-name">TANSWELL</span>
      </header>

      <h1 class="cover-title"><span class="title-accent">NOC</span> CAPABILITIES FRAMEWORK</h1>

      <p class="cover-intro">Welcome to a transformative solution designed to enhance the delivery of essential services in remote communities within the Northern Territories. At Tanswell Technology Services, we understand the unique challenges and responsibilities involved in providing reliable power and water services to these communities. This document outlines the core capabilities of our proposed Network Operations Centre (NOC) and how it can be a pivotal asset in achieving your mission.</p>

      <svg class="cover-visual" viewBox="0 430 1200 476" role="img" aria-label="Globe-shaped photograph of electricity transmission towers and power lines against a sunset sky, overlaid with a red circuit network pattern">
        <defs>
          <radialGradient id="domeGlow" cx="600" cy="1130" r="760" gradientUnits="userSpaceOnUse">
            <stop offset="0.78" stop-color="#ec1c24" stop-opacity="0.9"/>
            <stop offset="0.86" stop-color="#7a0a0e" stop-opacity="0.6"/>
            <stop offset="1" stop-color="#000000" stop-opacity="0"/>
          </radialGradient>
          <linearGradient id="domeSky" x1="0" y1="516" x2="0" y2="906" gradientUnits="userSpaceOnUse">
            <stop offset="0" stop-color="#6f9fd0"/>
            <stop offset="0.45" stop-color="#d9d3c0"/>
            <stop offset="0.8" stop-color="#f3c66a"/>
            <stop offset="1" stop-color="#e08a1e"/>
          </linearGradient>
        </defs>
        <rect x="0" y="430" width="1200" height="476" fill="url(#domeGlow)"/>
        <ellipse cx="600" cy="1116" rx="700" ry="600" fill="url(#domeSky)"/>
      </svg>
    </section>
  </main>
</body>
</html>
```